Shopify Web-Page "Tiny-ThreadDays

We are building a new business in Switzerland offering premium sewing holiday camps for kids aged 9–14. In enclosed brief outlines our requirements for a complete Shopify homepage design and a multilingual logo creation.
Domains: tiny-threaddays.ch ; tiny-giornifilo.ch ; tiny-fadentage.ch

Project Overview
We are looking for:
1. A modern, fully designed Shopify homepage in English using standard Shopify content blocks (no custom coding), which we can later update ourselves. Supporting Multilanguage (EN, German, Italian).

2. A logo design that includes the brand identity and communicates our multilingual, creative, and child-focused positioning.

All details in enclosed

```html
<!DOCTYPE html>
<html lang="en">
<head>
<meta charset="utf-8">
<title>Tiny-ThreadDays – Creative Sewing Camps for Kids</title>
<link rel="stylesheet" href="https://fonts.googleapis.com/css2?family=Archivo:wght@600;700;800&family=Plus+Jakarta+Sans:wght@400;500;600;700&display=swap">
<style>
:root{
  --orange:#ef5a1f;
  --ink:#111;
  --text:#333;
  --muted:#555;
  --light:#f3f2f4;
  --grey:#efefef;
  --navy:#111452;
  --white:#fff;
  --line:#9a9a9a;
}
*{box-sizing:border-box;margin:0;padding:0}
html,body{width:1200px;height:4267px;overflow:hidden}
body{font-family:"Plus Jakarta Sans",sans-serif;color:var(--text);background:var(--white);position:relative}
h1,h2,h3,h4{font-family:"Archivo",sans-serif;color:var(--ink);font-weight:800}
.abs{position:absolute}
.btn{position:absolute;background:var(--orange);color:var(--white);font-family:"Archivo",sans-serif;font-weight:700;display:flex;align-items:center;justify-content:center;text-transform:uppercase}
.rule{display:block;width:34px;height:3px;background:var(--ink)}
.center{left:0;width:1200px;text-align:center}
.center .rule{margin:0 auto}

/* header */
.site-header{position:absolute;top:0;left:0;width:1200px;height:91px;background:var(--white)}
.brand{position:absolute;left:152px;top:20px;display:flex;align-items:center;gap:12px}
.brand-dot{width:52px;height:52px;border-radius:50%;background:var(--orange)}
.brand-name{font-family:"Archivo",sans-serif;font-weight:700;font-size:23px;color:var(--ink)}
.nav{position:absolute;right:153px;top:33px;display:flex;gap:0;font-size:14px;font-weight:500;letter-spacing:.4px}
.nav a{color:var(--ink);text-decoration:none;padding:4px 12px;margin-left:18px}
.nav a.active{color:var(--orange);border:1px solid var(--orange)}

/* hero */
.hero{position:absolute;top:91px;left:0;width:1200px;height:587px;background:linear-gradient(100deg,#3a3b3c 0%,#7c7871 22%,#d6d1c8 45%,#cbbfb2 70%,#8f8a84 100%)}
.hero-veil{position:absolute;inset:0 0 auto 0;height:300px;background:linear-gradient(180deg,rgba(255,255,255,.85),rgba(255,255,255,0))}
.hero h1{top:40px;font-size:34px;letter-spacing:.3px}
.hero h1 span{color:var(--orange)}
.hero p{top:89px;font-size:14px;line-height:21px;color:var(--ink)}
.hero .btn{left:527px;top:152px;width:146px;height:44px;font-size:15px}
.dots{position:absolute;top:534px;left:563px;display:flex;gap:8px}
.dots i{width:11px;height:11px;border-radius:50%;background:var(--white)}
.dots i:first-child{background:var(--orange)}

/* welcome */
.welcome-img{left:152px;top:734px;width:430px;height:394px;background:linear-gradient(135deg,#e9ecef,#c9cdd3 50%,#a9927e)}
.welcome-text{left:630px;top:732px;width:420px}
.welcome-text h2{font-size:24px;line-height:34px;margin-bottom:18px}
.welcome-text h2 span{font-size:29px}
.welcome-text p{font-size:13px;line-height:22px;margin-top:16px;color:var(--ink)}
.welcome-text .rule{margin-bottom:26px;width:30px}
.welcome-btn{left:630px;top:1089px;width:121px;height:38px;font-size:13px}

/* how it works */
.how{position:absolute;top:1181px;left:0;width:1200px;height:428px;background:var(--light)}
.how h2{top:47px;font-size:29px}
.how .rule{margin-top:22px}
.steps{position:absolute;top:146px;left:151px;display:flex;gap:13px}
.step{width:169px;height:234px;background:var(--white);box-shadow:0 2px 8px rgba(0,0,0,.08);text-align:center;padding:30px 16px 0}
.step svg{width:52px;height:52px;stroke:var(--orange);fill:none;stroke-width:2}
.step h3{font-size:12.5px;margin-top:22px;font-weight:700}
.step p{font-size:11px;line-height:15px;margin-top:6px;color:var(--muted)}

/* why */
.why{left:148px;top:1668px;width:370px}
.why h2{font-size:29px;line-height:34px}
.why .rule{margin:22px 0 30px}
.why ul{list-style:none}
.why li{display:flex;gap:14px;font-size:13.5px;line-height:22px;margin-bottom:15px;color:var(--ink)}
.why li svg{flex:0 0 16px;width:16px;height:16px;margin-top:3px}
.why-img{left:548px;top:1667px;width:501px;height:436px;background:linear-gradient(120deg,#8a6a50,#d7c0a6 40%,#c58a7a 65%,#6f5a4e)}

/* upcoming */
.upcoming{position:absolute;top:2154px;left:0;width:1200px;height:655px;background:var(--grey)}
.upcoming h2{top:46px;font-size:29px}
.upcoming .rule{margin-top:22px}
.camp{position:absolute;top:144px;width:426px;height:463px;background:var(--white);box-shadow:0 2px 8px rgba(0,0,0,.08)}
.camp-img{height:297px}
.camp h3{font-size:23px;margin:24px 28px 10px}
.camp p{font-size:12px;line-height:18px;margin:0 28px;color:var(--muted)}

/* faq */
.faq-title{top:2855px;font-size:29px}
.faq-title .rule{margin-top:22px}
.faq{position:absolute;left:162px;top:2950px;width:880px;list-style:none}
.faq li{height:60px;border-bottom:2px solid var(--line);display:flex;align-items:center;justify-content:space-between;padding:0 24px 0 34px;font-size:18px;color:var(--ink)}
.faq li:last-child{border-bottom:none}
.faq svg{width:24px;height:24px}

/* cta */
.cta{position:absolute;top:3414px;left:0;width:1200px;height:298px;background:linear-gradient(100deg,#b8b8b6 0%,#e6e4e0 25%,#f2f0ee 50%,#e9e4df 75%,#c9c5c0 100%)}
.cta h2{top:72px;font-size:36px;line-height:49px}
.cta .btn{left:399px;top:187px;width:401px;height:51px;font-size:17px}

/* footer */
.site-footer{position:absolute;top:3712px;left:0;width:1200px;height:555px;background:var(--navy);color:var(--white)}
.site-footer h2{color:var(--white)}
.news{top:56px;font-size:28px}
.news-sub{top:102px;font-size:18px}
.news-form{position:absolute;left:328px;top:150px;width:544px;height:49px;border:1px solid rgba(255,255,255,.6);border-radius:25px;display:flex;align-items:center;justify-content:space-between;padding:0 20px 0 24px;font-size:14px}
.foot-col{position:absolute;top:245px;font-size:12.5px;line-height:21px}
.foot-col h4{color:var(--white);font-size:12.5px;font-weight:700;margin-bottom:12px}
.foot-col a{display:block;color:var(--white);text-decoration:none}
.contact-row{display:flex;gap:12px;margin-bottom:16px}
.contact-row svg{flex:0 0 14px;width:14px;height:14px;margin-top:4px;fill:var(--white)}
.foot-brand{position:absolute;left:850px;top:248px;width:202px;text-align:center}
.foot-brand i{display:block;width:56px;height:56px;border-radius:50%;background:var(--orange);margin:0 auto 18px}
.foot-brand b{font-family:"Archivo",sans-serif;font-size:20px;font-weight:700}
.socials{position:absolute;top:411px;left:528px;display:flex;gap:18px}
.socials i{width:14px;height:14px;border-radius:50%;background:var(--white)}
.foot-rule{position:absolute;left:152px;top:472px;width:896px;height:1px;background:rgba(255,255,255,.25)}
.copy{top:500px;font-size:12px;color:rgba(255,255,255,.8)}
</style>
</head>
<body>

<header class="site-header">
  <div class="brand"><span class="brand-dot"></span><span class="brand-name">Tiny-ThreadDays</span></div>
  <nav class="nav">
    <a class="active">HOME</a><a>ABOUT US</a><a>SERVICES</a><a>FAQ</a><a>CONTACT US</a>
  </nav>
</header>

<section class="hero" role="img" aria-label="Children working at sewing machines and a dress form in a bright attic sewing studio">
  <div class="hero-veil"></div>
  <h1 class="abs center">CREATIVE SEWING <span>CAMPS FOR KIDS</span></h1>
  <p class="abs center">Marta and Lena bring 10+ years of teaching experience to fun, structured sewing<br>workshops—small groups, big creativity, and a joyful fashion show finale!</p>
  <a class="btn">Read More</a>
  <div class="dots"><i></i><i></i><i></i><i></i></div>
</section>

<div class="abs welcome-img" role="img" aria-label="Girl sewing fabric at a white sewing machine by a window"></div>
<div class="abs welcome-text">
  <h2>WELCOME TO<br><span>TINY-THREADDAYS</span></h2>
  <span class="rule"></span>
  <p>Marta and Lena have over 10 years of experience in teaching children sewing, tailoring, and design with fun, style, and structure.</p>
  <p>In small groups (max. 8 children), we guide young talents through a creative week of vacation – with real results: self-sewn pieces, new friends, and lots of pride.</p>
  <p>At the last day, the children show off their success, their own sewn unique pieces, in a symapatic fashion show.</p>
</div>
<a class="btn welcome-btn">Read More</a>

<section class="how">
  <h2 class="abs center">HOW THE CAMP WORKS<span class="rule"></span></h2>
  <div class="steps">
    <div class="step">
      <svg viewBox="0 0 52 52"><rect x="6" y="8" width="20" height="36"/><path d="M26 20h20v24H26M12 8v36M18 8v36M32 28v16M38 28v16"/></svg>
      <h3>PROJECT SELECTION</h3><p>Your child chooses their own model based on previously produced clothing items and sewing patterns</p>
    </div>
    <div class="step">
      <svg viewBox="0 0 52 52"><path d="M6 20l20-8 20 8-20 8z M6 20v12l20 8 20-8V20 M6 26l20 8 20-8"/></svg>
      <h3>FABRIC SELECTION</h3><p>High-quality fabrics are available</p>
    </div>
    <div class="step">
      <svg viewBox="0 0 52 52"><path d="M10 12h30v10H22v18h20v6H8v-6h6V12"/><circle cx="34" cy="17" r="2"/><path d="M22 28h18v6"/></svg>
      <h3>SEWING MACHINE</h3><p>operation – Learn how to use a sewing machine</p>
    </div>
    <div class="step">
      <svg viewBox="0 0 52 52"><rect x="10" y="6" width="32" height="40"/><rect x="16" y="12" width="20" height="26"/><path d="M20 32l12-16"/></svg>
      <h3>SEWING &amp; REFINING</h3><p>Step by step to the goal with professional guidance</p>
    </div>
    <div class="step">
      <svg viewBox="0 0 52 52"><circle cx="26" cy="8" r="4"/><path d="M22 14h8l4 14H18zM18 28l-4 14h24l-4-14M26 42v6M8 14l2 2M44 14l-2 2"/></svg>
      <h3>SHOW TIME!</h3><p>Fashion show or photo shoot at the end of the week</p>
    </div>
  </div>
</section>

<div class="abs why">
  <h2>WHY PARENTS<br>CHOOSE US</h2>
  <span class="rule"></span>
  <ul>
    <li><svg viewBox="0 0 16 16" fill="none" stroke="#222" stroke-width="1.4"><rect x="1" y="1" width="14" height="14"/><path d="M4 8l3 3 5-6"/></svg>Small groups &amp; personalized attention</li>
    <li><svg viewBox="0 0 16 16" fill="none" stroke="#222" stroke-width="1.4"><rect x="1" y="1" width="14" height="14"/><path d="M4 8l3 3 5-6"/></svg>Multilingual supervision (DE / EN / IT)</li>
    <li><svg viewBox="0 0 16 16" fill="none" stroke="#222" stroke-width="1.4"><rect x="1" y="1" width="14" height="14"/><path d="M4 8l3 3 5-6"/></svg>High-quality fabrics &amp; top-quality sewing machines (Swiss-made)</li>
    <li><svg viewBox="0 0 16 16" fill="none" stroke="#222" stroke-width="1.4"><rect x="1" y="1" width="14" height="14"/><path d="M4 8l3 3 5-6"/></svg>Encouragement of creativity, self-confidence, and fine motor skills</li>
    <li><svg viewBox="0 0 16 16" fill="none" stroke="#222" stroke-width="1.4"><rect x="1" y="1" width="14" height="14"/><path d="M4 8l3 3 5-6"/></svg>Safe, loving environment in Zurich, various places easy to reach</li>
    <li><svg viewBox="0 0 16 16" fill="none" stroke="#222" stroke-width="1.4"><rect x="1" y="1" width="14" height="14"/><path d="M4 8l3 3 5-6"/></svg>Pick-up Service from the Main-Station</li>
  </ul>
</div>
<div class="abs why-img" role="img" aria-label="Instructor guiding children cutting fabric at a workshop table"></div>

<section class="upcoming">
  <h2 class="abs center">UPCOMING CAMP<span class="rule"></span></h2>
  <article class="camp" style="left:162px">
    <div class="camp-img" role="img" aria-label="Two children with measuring tapes choosing fabric in a sewing room" style="background:linear-gradient(120deg,#d9d6d2,#b8b3ad 50%,#e6dcc8)"></div>
    <h3>SPRING CAMPS</h3>
    <p>Lorem ipsum dolor sit amet, consectetur adipiscing elit, sed do eiusmod tempor incididunt ut labore et dolore magna aliqua. Ut enim ad minim veniam, quis nostrud exercitation</p>
  </article>
  <article class="camp" style="left:616px">
    <div class="camp-img" role="img" aria-label="Children drawing clothing patterns at a wooden table" style="background:linear-gradient(120deg,#8b8a78,#c7b59a 45%,#d8a35a 70%,#e9e2d6)"></div>
    <h3>SUMMER CAMPS</h3>
    <p>Lorem ipsum dolor sit amet, consectetur adipiscing elit, sed do eiusmod tempor incididunt ut labore et dolore magna aliqua. Ut enim ad minim veniam, quis nostrud exercitation</p>
  </article>
</section>

<h2 class="abs center faq-title">FAQ<span class="rule"></span></h2>
<ul class="faq">
  <li>What age group can join the sewing camp?<svg viewBox="0 0 24 24" fill="none" stroke="#222" stroke-width="1.4"><circle cx="12" cy="12" r="10"/><path d="M12 7v10M7 12h10"/></svg></li>
  <li>Do children need prior sewing experience?<svg viewBox="0 0 24 24" fill="none" stroke="#222" stroke-width="1.4"><circle cx="12" cy="12" r="10"/><path d="M12 7v10M7 12h10"/></svg></li>
  <li>How many children are in each group?<svg viewBox="0 0 24 24" fill="none" stroke="#222" stroke-width="1.4"><circle cx="12" cy="12" r="10"/><path d="M12 7v10M7 12h10"/></svg></li>
  <li>What materials are provided?<svg viewBox="0 0 24 24" fill="none" stroke="#222" stroke-width="1.4"><circle cx="12" cy="12" r="10"/><path d="M12 7v10M7 12h10"/></svg></li>
  <li>What will my child create during the camp?<svg viewBox="0 0 24 24" fill="none" stroke="#222" stroke-width="1.4"><circle cx="12" cy="12" r="10"/><path d="M12 7v10M7 12h10"/></svg></li>
  <li>How long is the camp?<svg viewBox="0 0 24 24" fill="none" stroke="#222" stroke-width="1.4"><circle cx="12" cy="12" r="10"/><path d="M12 7v10M7 12h10"/></svg></li>
  <li>Is there a final event for parents?<svg viewBox="0 0 24 24" fill="none" stroke="#222" stroke-width="1.4"><circle cx="12" cy="12" r="10"/><path d="M12 7v10M7 12h10"/></svg></li>
</ul>

<section class="cta" role="img" aria-label="Faded background of children sewing in a studio">
  <h2 class="abs center">UNLEASH YOUR CHILD’S<br>CREATIVITY THIS VACATION!</h2>
  <a class="btn">Register for the Sewing Camp Now</a>
</section>

<footer class="site-footer">
  <h2 class="abs center news">NEWSLTTER SUBSCRIBE</h2>
  <p class="abs center news-sub">Get More Details to Signup</p>
  <div class="news-form">Email id
    <svg width="36" height="14" viewBox="0 0 36 14" fill="none" stroke="#fff" stroke-width="1.5"><path d="M0 7h34M28 1l6 6-6 6"/></svg>
  </div>
  <div class="foot-col" style="left:157px">
    <h4>MENU</h4><a>Home</a><a>About Us</a><a>Services</a><a>FAQ</a><a>Contact Us</a>
  </div>
  <div class="foot-col" style="left:302px;width:220px">
    <h4>CONTACT US</h4>
    <div class="contact-row"><svg viewBox="0 0 14 14"><path d="M7 0a5 5 0 0 0-5 5c0 4 5 9 5 9s5-5 5-9a5 5 0 0 0-5-5zm0 7a2 2 0 1 1 0-4 2 2 0 0 1 0 4z"/></svg><span>12 Atelierweg,<br>8004 Zürich</span></div>
    <div class="contact-row"><svg viewBox="0 0 14 14"><path d="M3 0l3 3-2 2c1 2 3 4 5 5l2-2 3 3-2 3C6 14 0 8 0 3z"/></svg><span>+41 44 000 00 00</span></div>
    <div class="contact-row"><svg viewBox="0 0 14 14"><path d="M0 2h14v10H0z M0 2l7 6 7-6" stroke="#111452" stroke-width="1"/></svg><span>info@tiny-threaddays.ch</span></div>
  </div>
  <div class="foot-col" style="left:563px;width:230px;line-height:19px">
    <h4>OUR MISSION</h4>
    <p>Lorem ipsum dolor sit amet, consectetur adipiscing elit, sed do eiusmod tempor incididunt ut labore et dolore magna aliqua. Ut enim ad minim veniam, quis nostrud exercitation</p>
  </div>
  <div class="foot-brand"><i></i><b>Tiny-ThreadDays</b></div>
  <div class="socials"><i></i><i></i><i></i><i></i><i></i></div>
  <div class="foot-rule"></div>
  <p class="abs center copy">Copyright © 2025 All Rights Reserved</p>
</footer>

</body>
</html>
```